Climbing Gear Company Stationary Design

We need some new stationary to standardise our business.
We require:

Business Card
A4 Letterhead
With complements slip

Our business is a Distributor and retailer of rock climbing equipment throughout Australia.
We need to the stationary (business card in particular) to reflect this.

Target Market(s)

customers, other retail outlets, overseas manufacturers.

Industry/Entity Type

Business

Requirements
Must have
• company logo
website url- www.ridgetopgearworks.com.au
email - mark@ridgetopgearworks.com
Business Address: Unit 3, 14-16 Marlowe Street, Wren Harbour, QLD, 2371
Phone: 0438 627 194
my Name (on Business card) - Gordon Pellimore
use of Blue colour in our logo

```html
<!DOCTYPE html>
<html lang="en">
<head>
<meta charset="utf-8">
<title>Ridgetop Gearworks – Business Card</title>
<link rel="stylesheet" href="https://fonts.googleapis.com/css2?family=Open+Sans:ital,wght@0,400;0,700;1,700&display=swap">
<style>
  :root {
    --brand-blue: #233f8c;
    --card-white: #ffffff;
    --backdrop: #ece9e4;
    --name-grey: #3a3a3a;
    --divider: rgba(255,255,255,0.28);
  }
  html, body {
    margin: 0;
    padding: 0;
    width: 1200px;
    height: 440px;
    overflow: hidden;
    background: var(--backdrop);
    font-family: "Open Sans", Arial, sans-serif;
  }
  .canvas {
    position: relative;
    width: 1200px;
    height: 440px;
  }
  .card {
    position: absolute;
    width: 534px;
    height: 306px;
    border-radius: 18px;
    box-shadow: 0 6px 14px rgba(0,0,0,0.25);
    overflow: hidden;
  }
  .card--front {
    left: 52px;
    top: 62px;
    background: var(--card-white);
  }
  .card--back {
    left: 612px;
    top: 66px;
    background: var(--brand-blue);
  }
  .wordmark {
    position: absolute;
    margin: 0;
    color: var(--brand-blue);
    font-weight: 700;
    font-size: 37px;
    line-height: 1;
    letter-spacing: 0.6px;
    white-space: nowrap;
  }
  .tagline {
    position: absolute;
    margin: 0;
    color: var(--brand-blue);
    font-weight: 400;
    font-size: 15px;
    letter-spacing: 3.8px;
    white-space: nowrap;
  }
  .card--front .wordmark { left: 40px; top: 46px; }
  .card--front .tagline { left: 41px; top: 92px; }
  .holder-name {
    position: absolute;
    left: 28px;
    top: 199px;
    margin: 0;
    color: var(--name-grey);
    font-weight: 700;
    font-style: italic;
    font-size: 19px;
    letter-spacing: -0.3px;
    text-transform: uppercase;
  }
  .contact-panel {
    position: absolute;
    left: 266px;
    top: 149px;
    width: 240px;
    height: 131px;
    background: var(--brand-blue);
    border-radius: 14px;
    box-shadow: 0 6px 8px rgba(0,0,0,0.35);
    color: #fff;
    font-size: 13px;
    line-height: 18px;
  }
  .contact-group {
    padding: 4px 10px 5px;
    border-bottom: 1px solid var(--divider);
  }
  .contact-group:first-child { padding-top: 12px; }
  .contact-group:last-child { border-bottom: none; padding-top: 6px; }
  .contact-web { font-size: 12.5px; white-space: nowrap; }
  .contact-line {
    display: flex;
    align-items: center;
    gap: 6px;
  }
  .contact-line svg { flex: none; }
  .brand-band {
    position: absolute;
    left: 0;
    top: 132px;
    width: 100%;
    height: 88px;
    background: var(--card-white);
  }
  .card--back .wordmark { left: 58px; top: 15px; }
  .card--back .tagline { left: 59px; top: 58px; }
</style>
</head>
<body>
<main class="canvas">
  <section class="card card--front" aria-label="Business card front">
    <h1 class="wordmark">RIDGETOP GEARWORKS</h1>
    <p class="tagline">THE KIT&#8226;THE CLIMB&#8226;THE HIGH LIFE</p>
    <p class="holder-name">Gordon Pellimore</p>
    <div class="contact-panel">
      <div class="contact-group">
        <div class="contact-line">
          <svg width="10" height="11" viewBox="0 0 10 11" aria-hidden="true"><path d="M2 1 L4 1 L4.6 3.4 L3.3 4.3 Q4.3 6.6 6.4 7.6 L7.3 6.4 L9.4 7 L9.4 9 Q9 10.4 7.5 10.2 Q1 8.6 0.8 2.4 Q0.8 1 2 1 Z" fill="#fff"/></svg>
          <span>0438 627 194</span>
        </div>
        <div class="contact-line">
          <svg width="11" height="9" viewBox="0 0 11 9" aria-hidden="true"><rect x="0.6" y="0.6" width="9.8" height="7.8" fill="none" stroke="#fff" stroke-width="1.2"/><path d="M0.8 1 L5.5 5 L10.2 1" fill="none" stroke="#fff" stroke-width="1.2"/></svg>
          <span>mark@ridgetopgearworks.com</span>
        </div>
      </div>
      <div class="contact-group">
        <div>Unit 3, 14-16 Marlowe Street</div>
        <div>Wren Harbour, QLD, 2371</div>
      </div>
      <div class="contact-group contact-web">
        <div>www.RIDGETOPGEARWORKS.COM.au</div>
      </div>
    </div>
  </section>

  <section class="card card--back" aria-label="Business card back">
    <div class="brand-band">
      <p class="wordmark">RIDGETOP GEARWORKS</p>
      <p class="tagline">THE KIT&#8226;THE CLIMB&#8226;THE HIGH LIFE</p>
    </div>
  </section>
</main>
</body>
</html>
```